Redesign current business card for food company

i would like to redesign my business card. our company is food company, our product range from chips, juices, milk and etc (mostly dried food stuff).
I want o keep same logo but , the rest is open to new design.
you can check at our website about our company www.orvelpantry.com

Target Market(s)

most of food company

Industry/Entity Type

Business

Contact Information for Business Card

I want to keep more to blue color...

Colors
3176b5
abd036

Requirements
Must have
• our old logo
Nice to have
• we do not mind to have nice material on bus card in order to accomplish nice design. for example: using spot uv, embossed and etc.

```html
<!DOCTYPE html>
<html lang="en">
<head>
<meta charset="utf-8">
<title>Orvel Pantry Business Card</title>
<link rel="stylesheet" href="https://fonts.googleapis.com/css2?family=Source+Sans+3:wght@400;600;700&display=swap">
<style>
  :root {
    --page-bg: #ebe7e3;
    --blue-top: #178bd2;
    --blue-bottom: #1c5ea4;
    --blue-glow: rgba(40, 120, 240, 0.55);
    --orange-top: #f8a51b;
    --yellow-bottom: #fcd61c;
    --orange-glow: rgba(255, 236, 60, 0.75);
    --white: #ffffff;
    --brand-blue: #1f6cbd;
  }
  html, body {
    margin: 0;
    padding: 0;
    width: 1200px;
    height: 900px;
    overflow: hidden;
    background: var(--page-bg);
    font-family: "Source Sans 3", "Myriad Pro", Arial, sans-serif;
  }
  .canvas {
    position: relative;
    width: 1200px;
    height: 900px;
  }
  .card {
    position: absolute;
    overflow: hidden;
    box-shadow: 0 6px 18px rgba(0, 0, 0, 0.18);
  }
  .card--front {
    left: 78px;
    top: 35px;
    width: 587px;
    height: 362px;
    background: linear-gradient(180deg, var(--blue-top), var(--blue-bottom));
    color: var(--white);
    text-align: center;
  }
  .card--front .glow {
    position: absolute;
    left: -120px;
    top: 10px;
    width: 360px;
    height: 380px;
    background: radial-gradient(ellipse at 45% 50%, var(--blue-glow), rgba(40, 120, 240, 0) 70%);
  }
  .card--back {
    left: 388px;
    top: 505px;
    width: 567px;
    height: 352px;
    background: linear-gradient(180deg, var(--orange-top), var(--yellow-bottom));
  }
  .card--back .glow {
    position: absolute;
    right: -110px;
    top: -10px;
    width: 380px;
    height: 380px;
    background: radial-gradient(ellipse at 50% 50%, var(--orange-glow), rgba(255, 236, 60, 0) 70%);
  }
  .wordmark {
    position: absolute;
    font-weight: 600;
    font-size: 84px;
    line-height: 1;
    letter-spacing: -1px;
    white-space: nowrap;
  }
  .card--front .wordmark {
    left: 0;
    right: 0;
    top: 32px;
    padding-left: 10px;
    color: var(--white);
  }
  .card--back .wordmark {
    left: 0;
    right: 0;
    top: 130px;
    text-align: center;
    color: var(--brand-blue);
  }
  .contact {
    position: absolute;
    left: 0;
    right: 0;
    top: 153px;
    padding-left: 10px;
  }
  .contact p { margin: 0; line-height: 1.2; }
  .contact .name { font-size: 20px; font-weight: 700; }
  .contact .role { font-size: 16px; margin-top: 2px; }
  .contact .email { font-size: 16px; margin-top: 18px; }
  .contact .web { font-size: 16px; margin-top: 3px; }
  .contact .address { font-size: 16px; margin-top: 13px; }
  .contact .phones { font-size: 16px; margin-top: 20px; }
  .phones b { font-weight: 700; }
  .phones .sep { margin: 0 6px; }
</style>
</head>
<body>
<main class="canvas">
  <section class="card card--front" aria-label="Business card front">
    <div class="glow"></div>
    <div class="wordmark">orvel</div>
    <div class="contact">
      <p class="name">Daniel Suwarno</p>
      <p class="role">President</p>
      <p class="email">Daniel@orvelpantry.com</p>
      <p class="web">www.orvelpantry.com</p>
      <p class="address">2418 W Alder St.Ridgefield CA 91740</p>
      <p class="phones"><b>P:</b> 909 555 0142<span class="sep">|</span><b>F:</b> 909 555 0143<span class="sep">|</span><b>C:</b> 626 555 0178</p>
    </div>
  </section>
  <section class="card card--back" aria-label="Business card back">
    <div class="glow"></div>
    <div class="wordmark">orvel</div>
  </section>
</main>
</body>
</html>
```